Delivery Performance Dashboard for Web Portal

We need you to design a dashboard for our web portal. We deliver sand and stone to construction jobsites. The attached screenshot is from our current web portal dashboard . It shows how much material has been delivered from an order.

Dump trucks will deliver multiple loads during the day and the dispatcher uses the dashboard to monitor if they need to add more trucks or less trucks to fulfill the order. An example would be, I need to ship 1,000 tons of sand to a jobsite and I plan to use 10 trucks during the day and that it will take 10 hours of hauling to complete the job. After 5 hours of hauling (50% the day is over), I should have delivered 500 tons of sand (50% of the order). But maybe there is a lot of traffic, and I only have delivered 300 tons. The dashboard will show that I am behind schedule and I might need to add 2 more trucks to the job.

Industry/Entity Type

Construction

Font styles to use
Sans Serif

Requirements
Must have
• We need a progress bar showing how much material has been delivered, how much material was requested to be delivered total and how much material should have been delivered at the current time. The goal is to show the user if the deliveries are ahead or behind the expected pace and why.
Nice to have
• The icons for plant, driving and jobsite show if the actual times have exceeded or beaten the planned times. Maybe you have other ideas to show the user if the trucks are sitting longer on the jobsite, at the plant to get loaded or driving to and from the jobsite.

```html
<!DOCTYPE html>
<html lang="en">
<head>
<meta charset="utf-8">
<title>Delivery Performance Dashboard</title>
<link href="https://fonts.googleapis.com/css2?family=Roboto:wght@300;400;500&display=swap" rel="stylesheet">
<style>
:root{
  --brand:#4f92f1;
  --brand-text:#4a8fe6;
  --bg:#f6f7fb;
  --white:#ffffff;
  --ink:#1d1d1f;
  --muted:#9aa0a8;
  --line:#e3e6ec;
  --track:#e8ebf0;
  --good:#27b81c;
  --bad:#e0201b;
}
*{box-sizing:border-box;margin:0;padding:0}
html,body{width:1200px;height:517px;overflow:hidden}
body{font-family:"Roboto",sans-serif;background:var(--bg);color:var(--ink);position:relative}
.topbar{position:absolute;left:0;top:0;width:1200px;height:33px;background:var(--white)}
.menu-btn{position:absolute;left:13px;top:14px}
.top-actions{position:absolute;left:960px;top:8px}
.user-name{position:absolute;left:1017px;top:15px;font-size:4.5px;font-weight:500;text-align:right;line-height:1.1}
.user-name span{display:block;color:var(--brand);font-size:3px}
.avatar{position:absolute;left:1047px;top:7px;width:25px;height:25px;border-radius:50%;background:linear-gradient(135deg,#b08a70,#5b6a60)}
.sidebar{position:absolute;left:0;top:33px;width:36px;height:484px;background:var(--brand)}
.nav-active{position:absolute;left:34px;top:29px;width:2px;height:31px;background:var(--white)}
.nav-icon{position:absolute;left:13px}
.page-title{position:absolute;left:58px;top:58px;font-size:16px;font-weight:500;color:var(--brand-text)}
.search{position:absolute;left:203px;top:56px;width:231px;height:21px;display:flex}
.search-input{flex:1;background:var(--white);font-size:8px;color:#555;padding:6px 11px}
.search-btn{width:55px;background:var(--brand);display:flex;align-items:center;justify-content:center}
.select{position:absolute;top:56px;width:188px;height:21px;background:var(--white);font-size:8px;color:#555;padding:6px 13px}
.select::after{content:"";position:absolute;right:13px;top:9px;border:3.5px solid transparent;border-top:4px solid var(--brand)}
.section-label{position:absolute;left:58px;top:101px;font-size:10px;font-weight:300;color:var(--brand-text)}
.table{position:absolute;left:58px;top:124px;width:980px}
.row{position:absolute;left:0;width:951px;height:36px;font-size:8.2px;border-bottom:0.7px solid var(--line)}
.row.head{height:18px;top:0}
.cell{position:absolute;top:50%;transform:translateY(-50%);white-space:nowrap}
.check{width:10px;height:10px;background:var(--white);border-radius:2px;box-shadow:0 0 1px rgba(0,0,0,.25)}
.tons{width:112px}
.tons-meta{display:flex;justify-content:space-between;font-size:3.6px;color:var(--muted)}
.tons-meta .plan{color:var(--brand)}
.track{margin-top:4px;height:2.4px;background:var(--track);border-radius:2px}
.fill{height:100%;background:var(--brand);border-radius:2px}
.pos{color:var(--good)}
.neg{color:var(--bad)}
.overview{position:absolute;left:1096px;top:64px}
.ov-title{font-size:10.5px;margin-bottom:20px}
.ov-label{font-size:8px}
.ov-value{font-size:13.5px;margin:4px 0 14px}
.ov-value sup{font-size:4.5px;color:var(--bad);margin-left:4px}
.pager{position:absolute;left:1110px;top:493px;font-size:5.5px;color:#444}
.scroll{position:absolute;left:1193px;top:35px;width:2px;height:280px;background:var(--brand);border-radius:1px}
</style>
</head>
<body>
<svg width="0" height="0" style="position:absolute">
  <defs>
    <symbol id="plant" viewBox="0 0 12 9"><path d="M0 9V3l3 2V2l3 3V0h2v2l2-1v8z" fill="#4f92f1"/></symbol>
    <symbol id="truck" viewBox="0 0 12 8"><path d="M0 1h7v5H0zM7 3h3l2 2v1H7z" fill="#4f92f1"/><circle cx="2.5" cy="7" r="1" fill="#4f92f1"/><circle cx="9.5" cy="7" r="1" fill="#4f92f1"/></symbol>
    <symbol id="pin" viewBox="0 0 8 10"><path d="M4 10C1 6 0 4.5 0 3.5a4 4 0 018 0C8 4.5 7 6 4 10z" fill="#4f92f1"/><circle cx="4" cy="3.6" r="1.4" fill="#fff"/></symbol>
    <symbol id="up" viewBox="0 0 4 3"><path d="M0 3L2 0l2 3z" fill="#e0201b"/></symbol>
    <symbol id="upg" viewBox="0 0 4 3"><path d="M0 3L2 0l2 3z" fill="#27b81c"/></symbol>
    <symbol id="down" viewBox="0 0 4 3"><path d="M0 0h4L2 3z" fill="#27b81c"/></symbol>
    <symbol id="eye" viewBox="0 0 12 7"><path d="M0 3.5C2 0 10 0 12 3.5 10 7 2 7 0 3.5z" fill="#555"/><circle cx="6" cy="3.5" r="1.6" fill="#fff"/></symbol>
    <symbol id="waits" viewBox="0 0 52 10">
      <use href="#plant" x="0" y="1" width="11" height="8"/><use href="#up" x="12" y="5" width="3.5" height="3"/>
      <use href="#truck" x="18" y="1" width="11" height="8"/><use href="#upg" x="31" y="5" width="3.5" height="3"/>
      <use href="#pin" x="37" y="0" width="7" height="9"/><use href="#down" x="46" y="6" width="3.5" height="3"/>
    </symbol>
  </defs>
</svg>

<header class="topbar">
  <svg class="menu-btn" width="12" height="7" viewBox="0 0 12 7"><path d="M0 .5h12M0 3.5h12M0 6.5h12" stroke="#4f92f1" stroke-width="1.1"/></svg>
  <svg class="top-actions" width="40" height="16" viewBox="0 0 40 16">
    <circle cx="6" cy="8" r="3.8" fill="none" stroke="#999" stroke-width="1"/><path d="M9 11l2 2" stroke="#999"/>
    <path d="M26 12h8M27 12V8a3 3 0 016 0v4" fill="none" stroke="#999" stroke-width="1"/><circle cx="30" cy="13.5" r="1" fill="#999"/><circle cx="35" cy="4" r="1.4" fill="#4f92f1"/>
  </svg>
  <div class="user-name">Elias Marsh<span>Manager</span></div>
  <div class="avatar" role="img" aria-label="User profile photo"></div>
</header>

<nav class="sidebar">
  <div class="nav-active"></div>
  <svg class="nav-icon" style="top:40px" width="10" height="10" viewBox="0 0 10 10"><path d="M1 4.5L5 1l4 3.5V9H1z" fill="none" stroke="#fff"/></svg>
  <svg class="nav-icon" style="top:76px" width="10" height="10" viewBox="0 0 10 10"><path d="M5 .8l1.3 2.7 3 .4-2.2 2 .6 3L5 7.5 2.3 8.9l.6-3-2.2-2 3-.4z" fill="none" stroke="#fff"/></svg>
  <svg class="nav-icon" style="top:110px" width="10" height="10" viewBox="0 0 10 10"><path d="M6 2H1.5v7h7V4.5" fill="none" stroke="#fff"/><circle cx="8.2" cy="1.8" r="1.3" fill="#fff"/></svg>
  <svg class="nav-icon" style="top:149px" width="10" height="10" viewBox="0 0 10 10"><path d="M1 2h3l1 1.2h4V8.5H1z" fill="none" stroke="#fff"/></svg>
  <svg class="nav-icon" style="top:189px" width="10" height="10" viewBox="0 0 10 10"><circle cx="5" cy="3.3" r="2.3" fill="none" stroke="#fff"/><path d="M1 9.5a4 3.5 0 018 0z" fill="none" stroke="#fff"/></svg>
</nav>

<h1 class="page-title">Order : 17746</h1>
<div class="search">
  <div class="search-input">Search order number...</div>
  <div class="search-btn"><svg width="11" height="11" viewBox="0 0 11 11"><circle cx="4.6" cy="4.6" r="3.6" fill="none" stroke="#fff" stroke-width="1.3"/><path d="M7.3 7.3l2.8 2.8" stroke="#fff" stroke-width="1.3"/></svg></div>
</div>
<div class="select" style="left:449px">All</div>
<div class="select" style="left:650px">To Date</div>
<div class="select" style="left:853px;padding-left:20px">From Date</div>

<div class="section-label">Active Now</div>

<section class="table">
  <div class="row head">
    <span class="cell" style="left:0">#</span>
    <span class="cell" style="left:24px">Order id</span>
    <span class="cell" style="left:105px">Orgin</span>
    <span class="cell" style="left:224px">Destination</span>
    <span class="cell" style="left:363px">Customer</span>
    <span class="cell" style="left:547px">Status</span>
    <span class="cell" style="left:630px">Tons</span>
    <span class="cell" style="left:775px">Wait Times</span>
    <span class="cell" style="left:851px">Remaining</span>
    <span class="cell" style="left:913px">+/- <svg width="11" height="7" viewBox="0 0 12 8"><use href="#truck"/></svg></span>
  </div>
</section>

<section class="table" id="rows">
  <div class="row" style="top:19px"><span class="cell check"></span><span class="cell" style="left:24px">88038</span><span class="cell" style="left:105px">Ridgeway Aggregate Plant</span><span class="cell" style="left:224px">KTJV - i85 from mm 77 - 88</span><span class="cell" style="left:363px">Harlan Builders - North Division</span><span class="cell" style="left:547px">Accepted</span><div class="cell tons" style="left:630px"><div class="tons-meta"><span>722.57 / 1500</span><span class="plan">7:30AM - 5:00PM</span></div><div class="track"><div class="fill" style="width:60%"></div></div></div><svg class="cell" style="left:775px" width="52" height="10"><use href="#waits"/></svg><span class="cell pos" style="left:851px">+1:25 hrs</span><span class="cell neg" style="left:927px">-31</span><svg class="cell" style="left:965px" width="8" height="5"><use href="#eye"/></svg></div>
  <div class="row" style="top:55px"><span class="cell check"></span><span class="cell" style="left:24px">88038</span><span class="cell" style="left:105px">Ridgeway Aggregate Plant</span><span class="cell" style="left:224px">KTJV - i85 from mm 77 - 88</span><span class="cell" style="left:363px">Harlan Builders - North Division</span><span class="cell" style="left:547px">Accepted</span><div class="cell tons" style="left:630px"><div class="tons-meta"><span>5722.57 / 500</span><span class="plan">7:30AM - 5:00PM</span></div><div class="track"><div class="fill" style="width:40%"></div></div></div><svg class="cell" style="left:775px" width="52" height="10"><use href="#waits"/></svg><span class="cell pos" style="left:851px">+1:25 hrs</span><span class="cell pos" style="left:927px">+34</span><svg class="cell" style="left:965px" width="8" height="5"><use href="#eye"/></svg></div>
  <div class="row" style="top:92px"><span class="cell check"></span><span class="cell" style="left:24px">88038</span><span class="cell" style="left:105px">Ridgeway Aggregate Plant</span><span class="cell" style="left:224px">KTJV - i85 from mm 77 - 88</span><span class="cell" style="left:363px">Harlan Builders - North Division</span><span class="cell" style="left:547px">Accepted</span><div class="cell tons" style="left:630px"><div class="tons-meta"><span>722.57 / 1500</span><span class="plan">7:30AM - 5:00PM</span></div><div class="track"><div class="fill" style="width:60%"></div></div></div><svg class="cell" style="left:775px" width="52" height="10"><use href="#waits"/></svg><span class="cell pos" style="left:851px">+1:25 hrs</span><span class="cell neg" style="left:927px">-31</span><svg class="cell" style="left:965px" width="8" height="5"><use href="#eye"/></svg></div>
  <div class="row" style="top:130px"><span class="cell check"></span><span class="cell" style="left:24px">88038</span><span class="cell" style="left:105px">Ridgeway Aggregate Plant</span><span class="cell" style="left:224px">KTJV - i85 from mm 77 - 88</span><span class="cell" style="left:363px">Harlan Builders - North Division</span><span class="cell" style="left:547px">Accepted</span><div class="cell tons" style="left:630px"><div class="tons-meta"><span>5722.57 / 500</span><span class="plan">7:30AM - 5:00PM</span></div><div class="track"><div class="fill" style="width:40%"></div></div></div><svg class="cell" style="left:775px" width="52" height="10"><use href="#waits"/></svg><span class="cell pos" style="left:851px">+1:25 hrs</span><span class="cell pos" style="left:927px">+34</span><svg class="cell" style="left:965px" width="8" height="5"><use href="#eye"/></svg></div>
  <div class="row" style="top:166px"><span class="cell check"></span><span class="cell" style="left:24px">88038</span><span class="cell" style="left:105px">Ridgeway Aggregate Plant</span><span class="cell" style="left:224px">KTJV - i85 from mm 77 - 88</span><span class="cell" style="left:363px">Harlan Builders - North Division</span><span class="cell" style="left:547px">Accepted</span><div class="cell tons" style="left:630px"><div class="tons-meta"><span>722.57 / 1500</span><span class="plan">7:30AM - 5:00PM</span></div><div class="track"><div class="fill" style="width:60%"></div></div></div><svg class="cell" style="left:775px" width="52" height="10"><use href="#waits"/></svg><span class="cell pos" style="left:851px">+1:25 hrs</span><span class="cell neg" style="left:927px">-31</span><svg class="cell" style="left:965px" width="8" height="5"><use href="#eye"/></svg></div>
  <div class="row" style="top:203px"><span class="cell check"></span><span class="cell" style="left:24px">88038</span><span class="cell" style="left:105px">Ridgeway Aggregate Plant</span><span class="cell" style="left:224px">KTJV - i85 from mm 77 - 88</span><span class="cell" style="left:363px">Harlan Builders - North Division</span><span class="cell" style="left:547px">Accepted</span><div class="cell tons" style="left:630px"><div class="tons-meta"><span>5722.57 / 500</span><span class="plan">7:30AM - 5:00PM</span></div><div class="track"><div class="fill" style="width:40%"></div></div></div><svg class="cell" style="left:775px" width="52" height="10"><use href="#waits"/></svg><span class="cell pos" style="left:851px">+1:25 hrs</span><span class="cell pos" style="left:927px">+34</span><svg class="cell" style="left:965px" width="8" height="5"><use href="#eye"/></svg></div>
  <div class="row" style="top:240px"><span class="cell check"></span><span class="cell" style="left:24px">88038</span><span class="cell" style="left:105px">Ridgeway Aggregate Plant</span><span class="cell" style="left:224px">KTJV - i85 from mm 77 - 88</span><span class="cell" style="left:363px">Harlan Builders - North Division</span><span class="cell" style="left:547px">Accepted</span><div class="cell tons" style="left:630px"><div class="tons-meta"><span>722.57 / 1500</span><span class="plan">7:30AM - 5:00PM</span></div><div class="track"><div class="fill" style="width:60%"></div></div></div><svg class="cell" style="left:775px" width="52" height="10"><use href="#waits"/></svg><span class="cell pos" style="left:851px">+1:25 hrs</span><span class="cell neg" style="left:927px">-31</span><svg class="cell" style="left:965px" width="8" height="5"><use href="#eye"/></svg></div>
  <div class="row" style="top:277px"><span class="cell check"></span><span class="cell" style="left:24px">88038</span><span class="cell" style="left:105px">Ridgeway Aggregate Plant</span><span class="cell" style="left:224px">KTJV - i85 from mm 77 - 88</span><span class="cell" style="left:363px">Harlan Builders - North Division</span><span class="cell" style="left:547px">Accepted</span><div class="cell tons" style="left:630px"><div class="tons-meta"><span>5722.57 / 500</span><span class="plan">7:30AM - 5:00PM</span></div><div class="track"><div class="fill" style="width:40%"></div></div></div><svg class="cell" style="left:775px" width="52" height="10"><use href="#waits"/></svg><span class="cell pos" style="left:851px">+1:25 hrs</span><span class="cell pos" style="left:927px">+34</span><svg class="cell" style="left:965px" width="8" height="5"><use href="#eye"/></svg></div>
  <div class="row" style="top:315px;height:41px"><span class="cell check"></span><span class="cell" style="left:24px">88038</span><span class="cell" style="left:105px">Ridgeway Aggregate Plant</span><span class="cell" style="left:224px">KTJV - i85 from mm 77 - 88</span><span class="cell" style="left:363px">Harlan Builders - North Division</span><span class="cell" style="left:547px">Accepted</span><div class="cell tons" style="left:630px"><div class="tons-meta"><span>722.57 / 1500</span><span class="plan">7:30AM - 5:00PM</span></div><div class="track"><div class="fill" style="width:60%"></div></div></div><svg class="cell" style="left:775px" width="52" height="10"><use href="#waits"/></svg><span class="cell pos" style="left:851px">+1:25 hrs</span><span class="cell neg" style="left:927px">-31</span><svg class="cell" style="left:965px" width="8" height="5"><use href="#eye"/></svg></div>
  <div class="row" style="top:356px;border-bottom:none"><span class="cell check"></span><span class="cell" style="left:24px">88038</span><span class="cell" style="left:105px">Ridgeway Aggregate Plant</span><span class="cell" style="left:224px">KTJV - i85 from mm 77 - 88</span><span class="cell" style="left:363px">Harlan Builders - North Division</span><span class="cell" style="left:547px">Accepted</span><div class="cell tons" style="left:630px"><div class="tons-meta"><span>5722.57 / 500</span><span class="plan">7:30AM - 5:00PM</span></div><div class="track"><div class="fill" style="width:40%"></div></div></div><svg class="cell" style="left:775px" width="52" height="10"><use href="#waits"/></svg><span class="cell pos" style="left:851px">+1:25 hrs</span><span class="cell pos" style="left:927px">+34</span><svg class="cell" style="left:965px" width="8" height="5"><use href="#eye"/></svg></div>
</section>

<aside class="overview">
  <div class="ov-title">OVERVIEW</div>
  <div class="ov-label">Orders Today</div><div class="ov-value">235</div>
  <div class="ov-label">Pending Orders</div><div class="ov-value">23</div>
  <div class="ov-label">Delivered</div><div class="ov-value">125<sup>-3%</sup></div>
  <div class="ov-label">Cancelled</div><div class="ov-value">25</div>
</aside>
<div class="pager">1-3 OF 3 &nbsp;‹ ›</div>
<div class="scroll"></div>
</body>
</html>
```